Meadow Kr Circle (company name is Meadow Kr Circle LLP)

management of homestay, hospitality something similar with https://www.dorvika.example

Target Market(s)

johor bahru market (Malaysia)

Contact Information for Business Card

Meadow Circle KR LLP

Logo Text

eyes catching, attractive, amazing, Nice, jaw dropping for design

Coding

Coded - Design and coding required

Number of Pages Required

5+ page

Colors

Designer to choose colors to be used in the design.

Requirements
Must have
• please change the short term proposal to our company logo and change the name from dorvika to meadow KR Circle LLP
• thanks
Nice to have
• please let me have eyes catching , jaw dropping design

```html
<!DOCTYPE html>
<html lang="en">
<head>
<meta charset="utf-8">
<title>Meadow Kr Circle — Short-Stay Management</title>
<link rel="stylesheet" href="https://fonts.googleapis.com/css2?family=Lato:wght@400;700;900&family=Open+Sans:wght@400;600;700&display=swap">
<style>
:root{
  --red:#f7475b;
  --teal:#136f78;
  --teal-btn:#14808b;
  --ink:#222;
  --grey:#666;
  --line:#d6d6d6;
  --white:#fff;
  --black:#000;
}
*{margin:0;padding:0;box-sizing:border-box}
html,body{width:1200px;height:2826px;overflow:hidden;background:var(--white)}
body{position:relative;font-family:"Open Sans",Arial,sans-serif;color:var(--ink)}

/* header */
.header{position:absolute;left:0;top:0;width:1200px;height:122px;background:var(--white)}
.brand{position:absolute;left:0;width:1200px;top:34px;text-align:center;font-family:"Lato",sans-serif;font-weight:700;font-size:34px;line-height:36px;color:var(--teal)}
.phone{position:absolute;left:860px;top:72px;display:flex;align-items:center;gap:6px;font-family:"Lato",sans-serif;font-weight:700;font-size:20px;color:var(--black)}
.nav{position:absolute;left:0;top:122px;width:1200px;height:64px;border-top:1px solid var(--line);border-bottom:1px solid var(--line);display:flex;padding-left:207px}
.nav a{display:flex;align-items:center;justify-content:center;font-family:"Lato",sans-serif;font-size:19px;color:#333;text-decoration:none;border-left:1px solid var(--line)}
.nav a:first-child{border-left:none;color:var(--red)}

/* hero */
.hero{position:absolute;left:0;top:186px;width:1200px;height:564px;background:linear-gradient(100deg,#2a2520 0%,#5a4a38 35%,#3d342c 60%,#6a625a 85%,#8a8480 100%)}
.hero-shade{position:absolute;inset:0;background:rgba(0,0,0,.28)}
.hero-brand{position:absolute;left:0;width:1200px;top:148px;text-align:center;font-family:"Lato",sans-serif;font-weight:700;font-size:56px;line-height:112px;color:var(--white);letter-spacing:1px}
.hero-sub{position:absolute;left:0;width:1200px;top:262px;text-align:center;font-family:"Lato",sans-serif;font-weight:700;font-size:24px;line-height:30px;color:var(--white)}
.hero-btn{position:absolute;left:505px;top:319px;width:198px;height:55px;background:var(--teal-btn);color:var(--white);font-family:"Lato",sans-serif;font-weight:900;font-size:19px;display:flex;align-items:center;justify-content:center}
.dots{position:absolute;left:565px;top:513px;display:flex;gap:10px}
.dots span{width:17px;height:17px;border:2px solid var(--white);border-radius:50%}
.dots span.on{background:var(--white)}

/* about + service */
.about{position:absolute;left:0;top:750px;width:600px;height:484px;background:linear-gradient(90deg,#f4f4f4 0%,#eef0f0 50%,#dfe9ec 70%,#f0f0f0 100%)}
.about-veil{position:absolute;inset:0;background:rgba(255,255,255,.45)}
.section-h{font-family:"Lato",sans-serif;font-weight:700;font-size:33px;line-height:40px}
.about .section-h{position:absolute;left:168px;top:60px;color:var(--black)}
.about p{position:absolute;left:168px;top:122px;width:395px;font-size:17.5px;line-height:25px;color:#333}
.outline-btn{position:absolute;border:2px solid var(--teal-btn);color:var(--teal);font-family:"Lato",sans-serif;font-weight:900;font-size:17px;display:flex;align-items:center;justify-content:center;letter-spacing:.3px}
.about .outline-btn{left:170px;top:348px;width:170px;height:50px}
.service{position:absolute;left:600px;top:750px;width:600px;height:484px;background:var(--red)}
.service .section-h{position:absolute;left:54px;top:60px;color:var(--white);font-size:29px}
.service-item{position:absolute;left:56px;width:470px;color:var(--white)}
.service-item h3{font-family:"Open Sans",sans-serif;font-weight:700;font-size:19px;line-height:26px}
.service-item p{font-size:15px;line-height:20px;margin-top:4px}

/* posts */
.posts-h{position:absolute;left:173px;top:1302px;color:var(--teal)}
.post-media{position:absolute;left:171px;width:360px;height:232px}
.post-title{position:absolute;left:558px;width:490px;font-family:"Lato",sans-serif;font-weight:700;font-size:23px;line-height:28px;color:var(--red)}
.post-text{position:absolute;left:558px;width:470px;font-size:16.5px;line-height:25px;color:var(--grey)}
.post-btn{left:556px;width:152px;height:45px;font-size:16px}

/* signup */
.signup{position:absolute;left:0;top:2336px;width:1200px;height:339px;background:linear-gradient(100deg,#1d8f93 0%,#249fa6 40%,#1b8c94 70%,#2aa0a8 100%)}
.signup-veil{position:absolute;inset:0;background:rgba(18,120,130,.35)}
.signup h2{position:absolute;left:0;width:1200px;top:80px;text-align:center;font-family:"Lato",sans-serif;font-weight:400;font-size:30px;color:var(--white);letter-spacing:.5px}
.signup p{position:absolute;left:300px;width:600px;top:126px;text-align:center;font-size:17px;line-height:24px;color:var(--white)}
.signup-field{position:absolute;left:279px;top:196px;width:460px;height:55px;background:var(--white);display:flex;align-items:center;gap:10px;padding-left:20px;font-size:16px;color:#333}
.signup-btn{position:absolute;left:739px;top:196px;width:171px;height:55px;background:var(--red);color:var(--white);font-family:"Lato",sans-serif;font-weight:900;font-size:19px;display:flex;align-items:center;justify-content:center}

/* footer */
.footer{position:absolute;left:0;top:2675px;width:1200px;height:151px;background:var(--black);color:var(--white);font-size:14px}
.footer-legal{position:absolute;left:164px;top:42px;line-height:28px}
.footer-address{position:absolute;left:760px;top:42px;display:flex;gap:14px;line-height:28px}
</style>
</head>
<body>

<header class="header">
  <div class="brand">MEADOW KR<br>CIRCLE</div>
  <div class="phone">
    <svg width="20" height="20" viewBox="0 0 24 24"><path fill="#f7475b" d="M6.6 10.8c1.4 2.8 3.8 5.1 6.6 6.6l2.2-2.2c.3-.3.7-.4 1-.2 1.1.4 2.3.6 3.6.6.6 0 1 .4 1 1V20c0 .6-.4 1-1 1C10.6 21 3 13.4 3 4c0-.6.4-1 1-1h3.5c.6 0 1 .4 1 1 0 1.3.2 2.5.6 3.6.1.3 0 .7-.2 1z"/></svg>
    +65 9000 4172
  </div>
</header>

<nav class="nav">
  <a style="width:106px">HOME</a>
  <a style="width:135px">ABOUT US</a>
  <a style="width:174px">OUR SERVICES</a>
  <a style="width:117px">WHY US</a>
  <a style="width:107px">BLOGS</a>
  <a style="width:134px">CONTACT</a>
</nav>

<section class="hero" role="img" aria-label="Photo of a modern hotel suite with bathroom and double bed">
  <div class="hero-shade"></div>
  <h1 class="hero-brand">MEADOW KR CIRCLE</h1>
  <div class="hero-sub">MAXIMIZE YOUR RENTAL INCOME</div>
  <div class="hero-btn">CLICK HERE</div>
  <div class="dots"><span></span><span class="on"></span><span></span></div>
</section>

<section class="about" role="img" aria-label="Bright photo of a white seaside bedroom">
  <div class="about-veil"></div>
  <h2 class="section-h">ABOUT US</h2>
  <p>We are a short-term rental management and provides hospitality services to help property owners maximise their rental income.<br>Our goal is to help you reap the most from your rental income without you having to do any of the hard work such as handle all the particular renting problems on Staylane, Roomquay.com, cleaning and dealing with tenants and guests</p>
  <div class="outline-btn">READ MORE</div>
</section>

<section class="service">
  <h2 class="section-h">FULL HOSPITALITY SERVICE</h2>
  <div class="service-item" style="top:112px">
    <h3>Answering Enquiries, Check-Ins / Outs</h3>
    <p>We will answer all guest's enquiries, meet them to handover key and verification check. We also provide 24hr on-call support</p>
  </div>
  <div class="service-item" style="top:236px">
    <h3>Cleaning, Laundry and Maintenance</h3>
    <p>We get the professional cleaning team to clean up the place after the guest checked-out every time</p>
  </div>
  <div class="service-item" style="top:344px">
    <h3>Marketing &amp; Optimization</h3>
    <p>We take professional photos and write persuasive copywriting to optimize your listing in order to get more booking.</p>
  </div>
</section>

<h2 class="section-h posts-h">RECENT POSTS</h2>

<div class="post-media" style="top:1379px;background:linear-gradient(90deg,#5a3a20,#a0703f 50%,#6b4526)" role="img" aria-label="Photo of a warm-lit hotel bedroom"></div>
<h3 class="post-title" style="top:1364px">Class aptent taciti sociosqu ad litora torquent per conubia nostra per inceptos</h3>
<p class="post-text" style="top:1434px">vugiat in pede Fusce tellus Sed metus augue convallis et vehicula ut pulvinar eu ante Integer orci tellus tristique vitae consequat nec Vivamus porttitor purus nisi eleifend libero a tempus libero lectus feugiat felis Morbi diam mauris</p>
<div class="outline-btn post-btn" style="top:1566px">READ MORE</div>

<div class="post-media" style="top:1684px;background:linear-gradient(90deg,#2a1a10,#b07a3a 55%,#f2e6d4)" role="img" aria-label="Photo of a guest having breakfast in bed"></div>
<h3 class="post-title" style="top:1670px">Donec convallis pede venenatis nibh Duis quam Nam eget lacus Aliquam erat</h3>
<p class="post-text" style="top:1740px">vugiat in pede Fusce tellus Sed metus augue convallis et vehicula ut pulvinar eu ante Integer orci tellus tristique vitae consequat nec Vivamus porttitor purus nisi eleifend libero a tempus libero lectus feugiat felis Morbi diam mauris</p>
<div class="outline-btn post-btn" style="top:1871px">READ MORE</div>

<div class="post-media" style="top:2001px;background:linear-gradient(90deg,#8a7360,#c9bcae 50%,#e3e0dc)" role="img" aria-label="Photo of a bright modern bedroom with a window"></div>
<h3 class="post-title" style="top:1987px">Pellentesque faucibus Ut accumsan ultricies elit Maecenas at justo id velit placerat molestie</h3>
<p class="post-text" style="top:2057px">vugiat in pede Fusce tellus Sed metus augue convallis et vehicula ut pulvinar eu ante Integer orci tellus tristique vitae consequat nec Vivamus porttitor purus nisi eleifend libero a tempus libero lectus feugiat felis Morbi diam mauris</p>
<div class="outline-btn post-btn" style="top:2188px">READ MORE</div>

<section class="signup" role="img" aria-label="Photo of a desk with a laptop, plant and coffee mug">
  <div class="signup-veil"></div>
  <h2>SIGN UP FOR OUR SPECIAL OFFERS</h2>
  <p>Class aptent taciti sociosqu ad litora torquent per conubia nostra per inceptos hymenaeos Proin nulla arcu nonummy luctus dictum eget</p>
  <div class="signup-field">
    <svg width="20" height="15" viewBox="0 0 20 15"><rect x="1" y="1" width="18" height="13" rx="1.5" fill="none" stroke="#f7475b" stroke-width="1.8"/><path d="M1.5 2l8.5 6.5L18.5 2" fill="none" stroke="#f7475b" stroke-width="1.8"/></svg>
    Email address
  </div>
  <div class="signup-btn">SUBSCRIBE</div>
</section>

<footer class="footer">
  <div class="footer-legal">© 2018 Company Name &nbsp;All right reserved<br>Terms of Use &nbsp;| &nbsp;Privacy Policy</div>
  <div class="footer-address">
    <svg width="16" height="22" viewBox="0 0 16 22" style="margin-top:4px"><path fill="#fff" d="M8 0C3.6 0 0 3.5 0 7.9 0 13.8 8 22 8 22s8-8.2 8-14.1C16 3.5 12.4 0 8 0zm0 11a3 3 0 1 1 0-6 3 3 0 0 1 0 6z"/></svg>
    <div>L12-05 Cedar Point, Jalan Seroja,<br>Taman Lumera, 80100 Johor Bahru.</div>
  </div>
</footer>

</body>
</html>
```